Business Card for Multi-Brand Sportswear Company

We are looking for a business card which represents our company and the multiple brands within it.

The company: Fen Athletics (LTD)
The brands: Fen, TavaPuni, ElmStretch, Grit and Rain

Employees using these cards would be representing Fen Athletics, rather than any of the individual brands. You will see a current design within the uploaded files, to give some inspiration. The actual text of the brands is not necessary, but the logos should be on there is some format.

Our creative minds on this are stretched, so we are looking for someone to make this their own, and show us what a good business card should look like.

We may like to get these printed with spot gloss, so keep that in mind with your designs.

www.fenathletics.co.uk

Industry/Entity Type

Business

Contact Information for Business Card

Leo Pemberton-Hale
Operations Manager
(+44) 1632 960 418
Leo@fenathletics.co.uk
www.fenathletics.co.uk

Font styles to use
Sans Serif
Other font styles liked:
• Eurostile

Colors
ffffff

Requirements
Nice to have
• Dark (black) background

```html
<!DOCTYPE html>
<html lang="en">
<head>
<meta charset="utf-8">
<title>Fen Athletics — Business Card</title>
<link rel="stylesheet" href="https://fonts.googleapis.com/css2?family=Saira:wght@400;500;600;700&display=swap">
<style>
  :root {
    --backdrop: #3b3b3b;
    --card: #ffffff;
    --ink: #111111;
    --band: #060606;
    --accent: #e8202a;
    --on-dark: #f2f2f2;
    --muted: #8a8a8a;
    --plum: #5d5068;
  }
  * { box-sizing: border-box; margin: 0; padding: 0; }
  html, body {
    width: 1105px; height: 1200px; overflow: hidden;
    background: var(--backdrop);
    font-family: "Saira", "Helvetica Neue", Arial, sans-serif;
  }
  .card {
    position: absolute; left: 196px; width: 720px; height: 412px;
    background: var(--card); overflow: hidden;
  }
  .card--front { top: 146px; }
  .card--back { top: 602px; }

  .wordmark {
    position: absolute; display: flex; align-items: center;
    color: var(--ink); font-weight: 600; letter-spacing: 0.04em; text-transform: uppercase;
  }
  .wordmark__square { background: var(--accent); flex: none; }
  .card--front .wordmark { left: 43px; top: 52px; font-size: 38px; gap: 14px; }
  .card--front .wordmark__square { width: 18px; height: 18px; }
  .card--back .wordmark { left: 0; right: 0; justify-content: center; top: 138px; font-size: 64px; gap: 22px; }
  .card--back .wordmark__square { width: 28px; height: 28px; }

  .name-tab { position: absolute; left: 367px; top: 187px; width: 353px; height: 81px; }
  .name-tab svg { position: absolute; inset: 0; }
  .name-tab__text { position: absolute; right: 43px; top: 10px; text-align: right; color: #fff; }
  .name-tab__name { font-size: 27px; font-weight: 600; line-height: 1.15; }
  .name-tab__role { font-size: 19px; font-weight: 400; line-height: 1.3; }

  .contact-band {
    position: absolute; left: 0; right: 0; bottom: 0; height: 144px;
    background: var(--band); color: var(--on-dark); font-size: 19px;
  }
  .contact-list { position: absolute; left: 43px; top: 26px; list-style: none; }
  .contact-list li { display: flex; align-items: center; gap: 10px; height: 28.5px; }
  .contact-list svg { width: 17px; height: 17px; fill: var(--accent); flex: none; }
  .address { position: absolute; right: 43px; top: 56px; text-align: right; font-style: normal; line-height: 28.5px; }

  .brand-row {
    position: absolute; left: 0; right: 0; top: 340px; height: 40px;
    display: flex; justify-content: space-around; align-items: center;
    padding: 0 30px; font-size: 21px; font-weight: 600;
  }
  .brand--tava { color: var(--muted); }
  .brand--elm { color: var(--plum); }
  .brand--grit { color: var(--accent); }
  .brand--fen { color: var(--ink); }
</style>
</head>
<body>

<section class="card card--front">
  <div class="wordmark"><span class="wordmark__square"></span>Fen Athletics</div>

  <div class="name-tab">
    <svg viewBox="0 0 353 81" width="353" height="81" aria-hidden="true">
      <path d="M0 81 L46 14 Q56 0 76 0 L353 0 L353 81 Z" fill="var(--accent)"/>
    </svg>
    <div class="name-tab__text">
      <p class="name-tab__name">Tom Haverley</p>
      <p class="name-tab__role">Managing Director</p>
    </div>
  </div>

  <div class="contact-band">
    <ul class="contact-list">
      <li>
        <svg viewBox="0 0 24 24" aria-hidden="true"><path d="M6.6 10.8a15.2 15.2 0 0 0 6.6 6.6l2.2-2.2c.3-.3.7-.4 1-.2 1.1.4 2.3.6 3.6.6.6 0 1 .4 1 1V20c0 .6-.4 1-1 1A17 17 0 0 1 3 4c0-.6.4-1 1-1h3.5c.6 0 1 .4 1 1 0 1.3.2 2.5.6 3.6.1.3 0 .7-.2 1z"/></svg>
        +44 (0)1632 960418
      </li>
      <li>
        <svg viewBox="0 0 24 24" aria-hidden="true"><path d="M2 5h20v14H2z M3.5 6.5 12 13l8.5-6.5" fill="var(--accent)"/><path d="M3 6.5 12 13l9-6.5" fill="none" stroke="var(--band)" stroke-width="1.6"/></svg>
        tom@fenathletics.co.uk
      </li>
      <li>
        <svg viewBox="0 0 24 24" aria-hidden="true"><circle cx="12" cy="12" r="10"/><path d="M2 12h20M12 2c3 3 3 17 0 20M12 2c-3 3-3 17 0 20" fill="none" stroke="var(--band)" stroke-width="1.4"/></svg>
        www.fenathletics.co.uk
      </li>
    </ul>
    <address class="address">
      Ashby Yard, Kelton<br>
      Marlow Vale, ZZ1 4QT
    </address>
  </div>
</section>

<section class="card card--back">
  <div class="wordmark"><span class="wordmark__square"></span>Fen Athletics</div>
  <div class="brand-row">
    <span class="brand brand--tava">TavaPuni</span>
    <span class="brand brand--elm">ElmStretch</span>
    <span class="brand brand--grit">Grit and Rain</span>
    <span class="brand brand--fen">Fen</span>
  </div>
</section>

</body>
</html>
```